Need a clean & modern homepage for an education site + opportunity for longer term work

Thanks for viewing our project. We are excited about this new website and we hope that we might build a relationship with designers as we work on this project. I provided quite a few details and requirements to help you more quickly create a design that meets our needs.
Who we are:
We are a website that discusses the importance of college accreditation and provides a directory of college programs.
What we need:
A homepage that meets the below requirements and is inspired by the examples provided
Definition of accredited:
ac·cred·it·ed [uh-kred-i-tid] adj.
1. officially recognized as meeting the essential requirements, as of academic excellence: accredited schools.
2. provided with official credentials, as by a government: an accredited diplomatic representative.
3. accepted as authoritative: an accredited theory.
Overall look and feel for the homepage:
- Clean, simple and modern
- Limited (or zero) pictures
- Utilize color blocks with text
- A trend seems to be longer vertical length homepages with lots of whitespace. I generally like this trend as long as the page is not way to tall.
Inspirations: Sites that have a similar look and feel to what I need.
http://lernvoxa.org/
http://www.campusmetrik.com/colleges/brantmoor-university/
http://quietfolding.org/
http://www.velostrahiring.com/
http://www.zunq.com/
http://sketches.bxv.com/
Items to be included on the homepage. Details below on each item.
- Top navigation
- Logo: Please leave a blank area for a logo. The logo has not been designed.
- Simple graphic/color block at the top that highlights a definition of “Accredited” – the definition should be formatted like it is being copy/pasted from a dictionary.
- Space for a video and small (50 word) written description of the video. You can use placeholder text.
- One section with 3 Paragraphs of content (each paragraph around 100 words) with a header at the top. You can use placeholder text but please create the formatting. At the end of the 3 paragraphs please have a “Read More” Note this shouldn't be 3 separate paragraphs with three read mores - it is 3 paragraphs with one read more at the end.
- An area with the header “Search Colleges by State” that has anchor text links to all 50 states.
Top navigation:
- Home
- States – with a subnav dropdown that includes all 50 US states.
- Programs – with a subnav dropdown that includes program titles (list below)
- Degrees - with a subnav dropdown that includes 5 degree levels (list below)
- Accreditation – no subnav
- Rankings – no subnav
- Resources – no subnav
Footer
- Link to about us, privacy, and a copyright www.url.com
Programs List for sub navigation
Accounting
Art
Bible
Business
Criminal Justice
Design
Education
Engineering
English
Law
LPN to RN
Management
Math
MBA
MPH
Medical Assisting
Military
Nursing
Occupational Therapy
Paralegal
Psychology
Pharmacy
RN to BSN
Radiology
Social Work
Sonography
Degrees list for sub navigation
Certificate
Associate
Bachelors
Masters
PhD
Thanks so much - looking forward to working with you!
Education

```html
<!DOCTYPE html>
<html lang="en">
<head>
<meta charset="utf-8">
<title>Accordlist Colleges Online — Home</title>
<link href="https://fonts.googleapis.com/css2?family=Montserrat:wght@400;600;700&family=Open+Sans:ital,wght@0,400;0,600;1,400&display=swap" rel="stylesheet">
<style>
:root{
  --green:#16a085;
  --green-dark:#0f7a66;
  --green-pale:#d7f5ee;
  --navy:#2c3e50;
  --navy-line:#4a5b6c;
  --ink:#2f3a44;
  --body:#4d5660;
  --light:#eceff0;
  --map:#b8e3da;
  --white:#ffffff;
  --muted:#c7ced6;
  --footer:#333333;
}
*{margin:0;padding:0;box-sizing:border-box}
html,body{width:1200px;height:3462px;overflow:hidden}
body{position:relative;font-family:"Open Sans",Arial,sans-serif;color:var(--body);background:var(--white)}
.section{position:relative;width:1200px}
.abs{position:absolute}
.heading{font-family:"Montserrat",Arial,sans-serif;font-weight:700;letter-spacing:1px;text-transform:uppercase}

/* header */
.site-header{height:148px;background:#fafafa}
.logo{left:138px;top:32px;font-family:"Montserrat",sans-serif;font-weight:700;font-size:44px;line-height:42px;color:var(--ink)}
.social{top:23px;display:flex;gap:9px;left:934px}
.social span{width:38px;height:38px;background:var(--navy);display:block}
.main-nav{top:92px;left:323px;display:flex;gap:27px;font-family:"Montserrat",sans-serif;font-size:16px;color:var(--ink);text-transform:uppercase}
.main-nav .has-sub::after{content:"▾";font-size:11px;margin-left:3px}

/* definition */
.definition{height:235px;background:var(--green)}
.word{left:138px;top:52px;font-family:"Montserrat",sans-serif;font-weight:600;font-size:40px;line-height:46px;color:var(--white)}
.phonetic{left:138px;top:92px;font-style:italic;font-size:29px;line-height:40px;color:var(--green-pale)}
.pos{left:140px;top:140px;font-style:italic;font-size:17px;color:var(--green-dark)}
.senses{left:471px;top:38px;width:500px;font-size:17px;line-height:26.5px;color:var(--white)}
.senses p+p{margin-top:24px}

/* features */
.features{height:461px;background:var(--navy);margin-top:-41px;clip-path:polygon(0 0,50% 41px,100% 0,100% 100%,0 100%)}
.feature{top:131px;width:260px;text-align:center;color:var(--muted)}
.feature svg{display:block;margin:0 auto 30px}
.feature h3{font-size:26px;line-height:32px;color:var(--white);margin-bottom:16px}
.feature p{font-size:13.5px;line-height:18.5px}
.btn{display:block;font-family:"Montserrat",sans-serif;font-weight:700;font-size:15px;letter-spacing:1.5px;text-transform:uppercase;text-align:center;color:var(--white);border:3px solid var(--white)}
.learn-more{left:517px;top:783px;width:168px;height:40px;line-height:34px;background:var(--navy);z-index:2}

/* video */
.video{height:593px;background:#fafafa}
.video h2{position:absolute;top:88px;width:100%;text-align:center;font-size:34px;color:var(--ink)}
.video-copy{left:138px;top:236px;width:340px;font-size:14.5px;line-height:27.7px;color:var(--ink)}
.player{left:545px;top:185px;width:517px;height:344px;background:#3a3a3a;border-radius:8px;overflow:hidden}
.player .screen{position:absolute;left:8px;top:8px;width:501px;height:288px;background:linear-gradient(135deg,#8c7a68,#b49a7e 45%,#5b4a3e)}
.play{position:absolute;left:238px;top:127px;width:44px;height:40px;background:#f4f4f4;border-radius:4px}
.play::after{content:"";position:absolute;left:16px;top:11px;border-left:15px solid #333;border-top:9px solid transparent;border-bottom:9px solid transparent}
.bar{position:absolute;left:16px;top:313px;width:418px;height:8px;background:#666;border-radius:4px}
.bar i{display:block;width:125px;height:8px;background:var(--green);border-radius:4px}
.knob{position:absolute;left:136px;top:308px;width:8px;height:18px;background:#fff;border-radius:2px}
.ctrl{position:absolute;top:310px;width:14px;height:14px;background:#ddd}

/* paragraphs */
.paragraphs{height:492px;background:var(--green);color:var(--white)}
.paragraphs h2{position:absolute;top:52px;width:100%;text-align:center;font-size:38px;line-height:46px}
.para-copy{left:138px;top:144px;width:947px;font-size:14px;line-height:25.4px}
.para-copy p+p{margin-top:37px}
.read-more{left:512px;top:397px;width:176px;height:46px;line-height:40px}

/* states */
.states{height:618px;background:var(--light)}
.us-map{left:150px;top:27px;width:880px;height:560px;background:var(--map);border-radius:60px 140px 160px 120px / 60px 120px 200px 160px;opacity:.85}
.states h2{position:absolute;top:88px;width:100%;text-align:center;font-size:31px;color:#3d4852}
.states h2 em{font-family:"Open Sans",sans-serif;font-weight:400;font-style:italic;text-transform:none;color:#55606a}
.state-col{top:198px;list-style:none;font-size:14.5px;line-height:33.2px;color:var(--ink)}

/* programs */
.programs{height:681px;background:var(--navy);margin-top:9px;color:var(--white)}
.programs h2{position:absolute;top:45px;width:100%;text-align:center;font-size:36px}
.program{top:135px;width:260px;text-align:center;font-size:26px;line-height:33px}
.program svg{display:block;margin:0 auto 16px}
.divider{left:0;top:318px;width:1200px;height:2px;background:var(--navy-line)}
.other{left:143px;top:355px;font-size:24px}
.prog-col{top:415px;list-style:none;font-family:"Montserrat",sans-serif;font-size:15px;line-height:33.2px;text-transform:uppercase}

/* trust */
.trust{height:190px;background:var(--light)}
.trust-label{left:138px;top:47px;font-family:"Montserrat",sans-serif;font-size:27px;letter-spacing:2px;color:var(--ink)}
.badge{top:44px;height:42px;background:#c4c9cd;border-radius:3px}

/* footer */
.site-footer{height:150px;background:var(--footer);margin-top:-75px;clip-path:polygon(0 0,50% 40px,100% 0,100% 100%,0 100%);color:var(--white);text-align:center;font-family:"Montserrat",sans-serif;font-weight:600;font-size:13px;letter-spacing:.5px}
.copyright{position:absolute;top:65px;width:100%}
.footer-links{position:absolute;top:117px;width:100%;font-size:12px}
</style>
</head>
<body>

<header class="section site-header">
  <div class="abs logo">LOGO<br>HERE</div>
  <div class="abs social" aria-label="Social links"><span></span><span></span><span></span></div>
  <nav class="abs main-nav">
    <span>Home</span><span class="has-sub">States</span><span class="has-sub">Programs</span><span class="has-sub">Degrees</span><span>Accreditation</span><span>Rankings</span><span>Resources</span>
  </nav>
</header>

<section class="section definition">
  <div class="abs word">ac·cred·it·ed</div>
  <div class="abs phonetic">[uh-kred-i-tid]</div>
  <div class="abs pos">adjective</div>
  <div class="abs senses">
    <p>1. A college, schools, or online programs that has been officially reviewed to ensure it meets rigorous education standards and qualifies for federal financial assistance</p>
    <p>2. Term that you will better understand after exploring Accordlist Colleges Online</p>
  </div>
</section>

<section class="section features">
  <div class="abs feature" style="left:135px">
    <svg width="80" height="74" viewBox="0 0 80 74" fill="none" stroke="#16a085" stroke-width="5"><rect x="14" y="16" width="52" height="26" rx="13" transform="rotate(-35 40 29)"/><path d="M28 46l-6 22 10-6 6 10 4-20"/></svg>
    <h3 class="heading">Rankings</h3>
    <p>Egestas amet nullam dis. Ullamcorper netus cum accumsan pellentesque cubilia diam. A luctus turpis Rutrum fames quam integer. Etiam porta diam</p>
  </div>
  <div class="abs feature" style="left:470px">
    <svg width="80" height="74" viewBox="0 0 80 74" fill="#16a085"><path d="M40 10L2 28l38 18 38-18z"/><path d="M18 38v18c8 8 36 8 44 0V38L40 49z"/><rect x="72" y="28" width="4" height="22"/></svg>
    <h3 class="heading">Accreditation</h3>
    <p>Massa commodo hendrerit blandit cras habitasse suspendisse eros pellentesque vel facilisis sodales, nulla volutpat conubia aliquet aptent eleifend commodo vitae hendrerit</p>
  </div>
  <div class="abs feature" style="left:805px">
    <svg width="80" height="74" viewBox="0 0 80 74" fill="#16a085"><path d="M40 4L4 22h72z"/><rect x="4" y="26" width="72" height="6"/><rect x="12" y="36" width="8" height="26"/><rect x="28" y="36" width="8" height="26"/><rect x="44" y="36" width="8" height="26"/><rect x="60" y="36" width="8" height="26"/><rect x="4" y="64" width="72" height="7"/></svg>
    <h3 class="heading">Resources</h3>
    <p>Iaculis fermentum pellentesque sociosqu amet aenean netus, donec laoreet luctus. Accumsan nullam habitant felis Erat morbi taciti elit cubilia dapibus enim</p>
  </div>
</section>
<a class="abs btn learn-more">Learn More</a>

<section class="section video">
  <h2 class="heading">Video Paragraph</h2>
  <p class="abs video-copy">Quam praesent. Ullamcorper dolor primis natoque dolor. Erat mollis. Aliquam facilisis. Vestibulum pharetra natoque pulvinar nec. Praesent risus, morbi lobortis odio pretium aptent. Hendrerit ligula varius iaculis nonummy enim. Pulvinar mauris quam eleifend, iaculis vestibulum cras, dui nullam vulputate eu Ridiculus sit platea quis mi. Cubilia netus purus nunc etiam.</p>
  <div class="abs player">
    <div class="screen" role="img" aria-label="Video still of a desk with books, a keyboard and a phone seen from above"></div>
    <div class="play"></div>
    <div class="bar"><i></i></div>
    <div class="knob"></div>
    <div class="ctrl" style="left:452px"></div>
    <div class="ctrl" style="left:478px"></div>
  </div>
</section>

<section class="section paragraphs">
  <h2 class="heading">Paragraphs Title</h2>
  <div class="abs para-copy">
    <p>Sed ut perspiciatis unde omnis iste natus error sit voluptatem accusantium doloremque laudantium, totam rem aperiam, eaque ipsa quae ab illo inventore veritatis et quasi architecto beatae vitae dicta sunt explicabo. Nemo enim ipsam voluptatem quia voluptas sit aspernatur aut odit aut fugit, sed quia consequuntur magni dolores eos qui ratione voluptatem sequi nesciunt. Neque porro quisquam est, qui dolorem ipsum quia dolor sit.</p>
    <p>Sed ut perspiciatis unde omnis iste natus error sit voluptatem accusantium doloremque laudantium, totam rem aperiam, eaque ipsa quae ab illo inventore veritatis et quasi architecto beatae vitae dicta sunt explicabo. Nemo enim ipsam voluptatem quia voluptas sit aspernatur aut odit aut fugit.</p>
  </div>
  <a class="abs btn read-more">Read More</a>
</section>

<section class="section states">
  <div class="abs us-map" role="img" aria-label="Map of the United States with state outlines"></div>
  <h2 class="heading">Search Colleges <em>by</em> State</h2>
  <ul class="abs state-col" style="left:138px"><li>Alabama</li><li>Alaska</li><li>Arizona</li><li>Arkansas</li><li>California</li><li>Colorado</li><li>Connecticut</li><li>Delaware</li><li>Florida</li><li>Georgia</li></ul>
  <ul class="abs state-col" style="left:342px"><li>Hawaii</li><li>Idaho</li><li>Illinois</li><li>Indiana</li><li>Iowa</li><li>Kansas</li><li>Kentucky</li><li>Louisiana</li><li>Maine</li><li>Maryland</li></ul>
  <ul class="abs state-col" style="left:526px"><li>Massachusetts</li><li>Michigan</li><li>Minnesota</li><li>Mississippi</li><li>Missouri</li><li>Montana</li><li>Nebraska</li><li>Nevada</li><li>New Hampshire</li><li>New Jersey</li></ul>
  <ul class="abs state-col" style="left:738px"><li>New Mexico</li><li>New York</li><li>North Carolina</li><li>North Dakota</li><li>Ohio</li><li>Oklahoma</li><li>Oregon</li><li>Pennsylvania</li><li>Rhode Island</li><li>South Carolina</li></ul>
  <ul class="abs state-col" style="left:932px"><li>South Dakota</li><li>Tennessee</li><li>Texas</li><li>Utah</li><li>Vermont</li><li>Virginia</li><li>Washington</li><li>West Virginia</li><li>Wisconsin</li><li>Wyoming</li></ul>
</section>

<section class="section programs">
  <h2 class="heading">Our Programs</h2>
  <div class="abs program" style="left:92px">
    <svg width="60" height="50" viewBox="0 0 60 50" fill="#fff"><circle cx="16" cy="30" r="15"/><rect x="28" y="4" width="30" height="5"/><rect x="28" y="13" width="30" height="5"/><rect x="30" y="22" width="28" height="5"/><rect x="32" y="31" width="26" height="5"/><rect x="30" y="40" width="28" height="5"/><path d="M16 20v20M12 24h7M12 36h7" stroke="#2c3e50" stroke-width="3"/></svg>
    Accounting<br>Programs
  </div>
  <div class="abs program" style="left:355px">
    <svg width="60" height="50" viewBox="0 0 60 50" fill="#fff"><path d="M30 2L2 16h56z"/><rect x="4" y="18" width="52" height="4"/><rect x="9" y="25" width="6" height="17"/><rect x="21" y="25" width="6" height="17"/><rect x="33" y="25" width="6" height="17"/><rect x="45" y="25" width="6" height="17"/><rect x="2" y="44" width="56" height="5"/></svg>
    Law<br>Programs
  </div>
  <div class="abs program" style="left:597px">
    <svg width="60" height="50" viewBox="0 0 60 50" fill="#fff"><rect x="21" y="3" width="18" height="10" rx="2" fill="none" stroke="#fff" stroke-width="4"/><rect x="4" y="11" width="52" height="36" rx="4"/><rect x="4" y="24" width="52" height="3" fill="#2c3e50"/><rect x="27" y="21" width="6" height="9" fill="#fff"/></svg>
    MBA<br>Programs
  </div>
  <div class="abs program" style="left:842px">
    <svg width="60" height="50" viewBox="0 0 60 50" fill="#fff"><rect x="22" y="4" width="16" height="42" rx="2"/><rect x="9" y="17" width="42" height="16" rx="2"/></svg>
    Nursing<br>Programs
  </div>
  <div class="abs divider"></div>
  <h3 class="abs heading other">Other Programs</h3>
  <ul class="abs prog-col" style="left:143px"><li>Accounting</li><li>Art</li><li>Bible</li><li>Business</li><li>Criminal Justice</li><li>Design</li><li>Education</li></ul>
  <ul class="abs prog-col" style="left:392px"><li>Engineering</li><li>English</li><li>Law</li><li>LPN to RN</li><li>Management</li><li>Math</li><li>MBA</li></ul>
  <ul class="abs prog-col" style="left:614px"><li>MPH</li><li>Medical Assisting</li><li>Military</li><li>Nursing</li><li>Occupational Therapy</li><li>Paralegal</li><li>Psychology</li></ul>
  <ul class="abs prog-col" style="left:891px"><li>Pharmacy</li><li>RN to BSN</li><li>Radiology</li><li>Social Work</li><li>Sonography</li></ul>
</section>

<section class="section trust">
  <div class="abs trust-label">TRUST</div>
  <div class="abs badge" style="left:300px;width:140px"></div>
  <div class="abs badge" style="left:492px;width:200px"></div>
  <div class="abs badge" style="left:762px;width:162px"></div>
  <div class="abs badge" style="left:958px;width:92px"></div>
</section>

<footer class="section site-footer">
  <div class="copyright">COPYRIGHT © 2013 WWW.ACCORDLIST.COM. ALL RIGHTS RESERVED.</div>
  <div class="footer-links">ABOUT US &nbsp;|&nbsp; PRIVACY</div>
</footer>

</body>
</html>
```